Wheels for Heroes Website Design

We need a NEW design and uploaded to Hostrova.com. Here is the current site: http://www.wheelsforheroes.org

Need a form like this:

https://youthautogifts.org/

Coding

Coded - Design and coding required

Number of Pages Required

1 page

```html
<!DOCTYPE html>
<html lang="en">
<head>
<meta charset="utf-8">
<title>Wheels for Heroes – Car Donation</title>
<link rel="stylesheet" href="https://fonts.googleapis.com/css2?family=Roboto:wght@300;400;500;700;900&display=swap">
<style>
:root{
  --red:#e1251b;
  --red-dark:#c41a12;
  --navy:#1c3a6b;
  --ink:#2b2f36;
  --muted:#6b7280;
  --line:#e3e6ea;
  --gray-bg:#f1f2f4;
  --blue:#3d72b8;
  --blue-dark:#2a5a9c;
  --white:#ffffff;
}
*{box-sizing:border-box;margin:0;padding:0}
html,body{width:1200px;height:3484px;overflow:hidden}
body{font-family:"Roboto",Arial,sans-serif;color:var(--ink);background:var(--white);position:relative}
a{color:inherit;text-decoration:none}

/* header */
.site-header{position:absolute;top:0;left:0;width:1200px;height:112px;background:var(--white);border-bottom:1px solid var(--line)}
.brand{position:absolute;left:40px;top:30px;display:flex;align-items:center;gap:12px}
.brand-dot{width:40px;height:40px;border-radius:50%;background:var(--red)}
.brand-name{font-size:28px;font-weight:700;color:var(--navy);text-transform:uppercase;letter-spacing:.5px}
.top-call{position:absolute;right:40px;top:14px;font-size:15px;color:var(--ink);display:flex;align-items:center;gap:8px}
.top-call strong{color:var(--red);font-size:18px}
.main-nav{position:absolute;right:40px;top:52px;display:flex;align-items:center;gap:26px;font-size:16px;font-weight:500}
.btn-red{display:inline-block;background:var(--red);color:var(--white);font-weight:700;text-transform:uppercase;border-radius:3px}
.main-nav .btn-red{padding:14px 20px;font-size:15px}

/* hero */
.hero{position:absolute;top:112px;left:0;width:1200px;height:600px;overflow:hidden}
.hero-photo{position:absolute;inset:0;background:linear-gradient(100deg,#8a9a7a 0%,#c9b49a 30%,#e9e2d8 55%,#f4f2ee 100%)}
.hero-shade{position:absolute;inset:0;background:linear-gradient(90deg,rgba(30,45,70,.55),rgba(30,45,70,.05) 55%)}
.hero-copy{position:absolute;left:60px;top:230px;color:var(--white)}
.hero-copy h1{font-size:64px;font-weight:500;line-height:1.05}
.hero-copy p{font-size:26px;font-weight:300;margin:12px 0 30px}
.btn-light{display:inline-block;background:var(--white);color:var(--navy);font-weight:700;font-size:16px;padding:16px 26px;border-radius:3px}

.donate-form{position:absolute;left:660px;top:70px;width:480px;height:430px;background:var(--white);border-radius:4px;box-shadow:0 6px 24px rgba(0,0,0,.18);padding:22px 30px}
.steps{display:flex;gap:30px;border-bottom:1px solid var(--line);padding-bottom:16px;margin-bottom:18px}
.step{display:flex;align-items:center;gap:10px;font-size:16px;color:#9aa1ab;flex:1}
.step b{width:30px;height:30px;border-radius:50%;background:#c9ced6;color:var(--white);display:flex;align-items:center;justify-content:center;font-size:15px}
.step.is-active{color:var(--navy);font-weight:500}
.step.is-active b{background:var(--navy)}
.field-label{font-size:16px;color:var(--ink);margin-bottom:10px}
.field-row{display:flex;gap:12px;margin-bottom:20px}
.select{flex:1;height:44px;border:1px solid var(--line);border-radius:3px;font-size:13px;color:#9aa1ab;display:flex;align-items:center;justify-content:space-between;padding:0 12px}
.select::after{content:"";border:5px solid transparent;border-top-color:#9aa1ab;margin-top:5px}
.labels3{display:flex;gap:12px}
.labels3 span{flex:1;font-size:16px}
.badges{display:flex;justify-content:center;gap:20px;margin:6px 0 24px}
.badge{width:44px;height:44px;border-radius:50%}
.form-submit{display:block;text-align:center;width:280px;margin:0 auto;padding:18px 0;font-size:16px}

/* sections */
.section-title{font-size:36px;font-weight:500;text-align:center;color:var(--ink)}

.how{position:absolute;top:712px;left:0;width:1200px;height:456px;padding-top:56px}
.how-steps{display:flex;justify-content:center;gap:60px;margin-top:46px}
.how-step{width:280px;text-align:center}
.how-icon{width:110px;height:100px;margin:0 auto}
.how-num{width:44px;height:44px;border:2px solid #b9bfc8;border-radius:50%;margin:22px auto 12px;display:flex;align-items:center;justify-content:center;font-size:20px;color:var(--muted)}
.how-step h3{font-size:22px;font-weight:500;margin-bottom:8px}
.how-step p{font-size:14px;color:var(--muted);line-height:1.5}

.impact{position:absolute;top:1168px;left:0;width:1200px;height:560px;background:var(--gray-bg);padding-top:52px}
.impact-cards{display:flex;justify-content:center;gap:40px;margin-top:40px}
.impact-card{width:300px;height:380px;background:var(--white);box-shadow:0 2px 8px rgba(0,0,0,.08);text-align:center}
.impact-photo{height:180px}
.impact-card h3{font-size:22px;font-weight:500;margin:22px 0 10px}
.impact-card p{font-size:13px;color:var(--muted);line-height:1.5;padding:0 28px}
.impact-card a{display:block;color:var(--red);font-weight:700;font-size:14px;margin-top:16px;text-transform:uppercase}

.why{position:absolute;top:1728px;left:0;width:1200px;height:560px;background:linear-gradient(135deg,var(--blue-dark),var(--blue));color:var(--white);overflow:hidden}
.why-photo{position:absolute;right:0;top:0;width:560px;height:560px;background:linear-gradient(160deg,#c9d6e6 0%,#8c8a6e 45%,#5a5a44 100%)}
.why-copy{position:absolute;left:110px;top:70px;width:520px}
.why-copy h2{font-size:36px;font-weight:500;margin-bottom:30px}
.why-list{list-style:none}
.why-list li{display:flex;gap:14px;font-size:15px;line-height:1.5;margin-bottom:20px}
.why-list svg{flex:0 0 20px;margin-top:2px}

.faq{position:absolute;top:2288px;left:0;width:1200px;height:760px;padding-top:70px}
.faq-list{width:880px;margin:44px auto 0;border:1px solid var(--line)}
.faq-item{border-bottom:1px solid var(--line);padding:20px 26px;display:flex;justify-content:space-between;align-items:center;font-size:18px}
.faq-item:last-child{border-bottom:0}
.faq-item svg{flex:0 0 14px}
.faq-item.is-open{display:block;background:#fafbfc}
.faq-item.is-open .faq-q{display:flex;justify-content:space-between;align-items:center}
.faq-item.is-open p{font-size:14px;color:var(--muted);line-height:1.6;margin-top:12px}

.site-footer{position:absolute;top:3048px;left:0;width:1200px;height:436px;background:var(--gray-bg)}
.footer-brand{position:absolute;left:40px;top:50px;width:320px}
.footer-brand .brand{position:static;margin-bottom:18px}
.footer-brand p{font-size:13px;color:var(--muted);line-height:1.6}
.footer-call{position:absolute;left:440px;top:56px;width:320px;text-align:center}
.footer-call small{font-size:15px;color:var(--muted)}
.footer-call strong{display:block;font-size:34px;color:var(--red);margin:6px 0}
.footer-call span{font-size:15px;color:var(--muted)}
.seals{display:flex;justify-content:center;gap:24px;margin-top:20px}
.seal{width:50px;height:50px;border-radius:50%;background:#c9d3de}
.seal.square{border-radius:4px;background:#d9b9b6}
.quick-links{position:absolute;left:900px;top:56px}
.quick-links h4{font-size:20px;font-weight:500;margin-bottom:10px}
.quick-links li{list-style:none;font-size:14px;color:var(--muted);line-height:1.7}
.footer-bar{position:absolute;left:40px;right:40px;bottom:0;height:80px;border-top:1px solid #d7dbe0;display:flex;justify-content:space-between;align-items:center}
.footer-bar small{font-size:13px;color:var(--muted)}
.social{display:flex;gap:12px}
.social span{width:36px;height:36px;border-radius:50%;border:1px solid var(--red)}
</style>
</head>
<body>

<header class="site-header">
  <a class="brand" href="#"><span class="brand-dot"></span><span class="brand-name">Wheels for Heroes</span></a>
  <div class="top-call">
    <svg width="16" height="16" viewBox="0 0 24 24"><path fill="#e1251b" d="M6.6 10.8a15.1 15.1 0 0 0 6.6 6.6l2.2-2.2a1 1 0 0 1 1-.25 11.4 11.4 0 0 0 3.6.57 1 1 0 0 1 1 1V20a1 1 0 0 1-1 1A17 17 0 0 1 3 4a1 1 0 0 1 1-1h3.5a1 1 0 0 1 1 1c0 1.25.2 2.45.57 3.57a1 1 0 0 1-.25 1z"/></svg>
    Call Today to Donate <strong>1-800-555-0142</strong>
  </div>
  <nav class="main-nav">
    <a href="#">About</a><a href="#">How to Donate</a><a href="#">Why Donate</a><a href="#">FAQs</a><a href="#">Contact</a>
    <a class="btn-red" href="#">Donate a Car</a>
  </nav>
</header>

<section class="hero">
  <div class="hero-photo" role="img" aria-label="Soldier in camouflage holding a smiling child"></div>
  <div class="hero-shade"></div>
  <div class="hero-copy">
    <h1>Car Donation<br>Made Easy</h1>
    <p>Join our 500,000+ donors</p>
    <a class="btn-light" href="#">JOIN US NOW!</a>
  </div>
  <form class="donate-form">
    <div class="steps">
      <div class="step is-active"><b>1</b>Vehicle Info</div>
      <div class="step"><b>2</b>Contact Info</div>
    </div>
    <div class="field-label">What kind of car?</div>
    <div class="field-row"><span class="select">Year</span><span class="select">Make</span><span class="select">Model</span></div>
    <div class="labels3 field-label"><span>Mileage</span><span>Does it Run?</span><span>Title Available?</span></div>
    <div class="field-row"><span class="select">Enter Mileage</span><span class="select">Select</span><span class="select">Select</span></div>
    <div class="badges">
      <span class="badge" style="background:#f08a3c"></span>
      <span class="badge" style="background:#c9ced6"></span>
      <span class="badge" style="background:#2aa6a0"></span>
    </div>
    <a class="btn-red form-submit" href="#">Donate My Vehicle Now!</a>
  </form>
</section>

<section class="how">
  <h2 class="section-title">How to Donate</h2>
  <div class="how-steps">
    <div class="how-step">
      <div class="how-icon" role="img" aria-label="Contact form and pen icon" style="background:linear-gradient(135deg,#1c3a6b,#3d72b8);border-radius:6px;width:80px"></div>
      <div class="how-num">1</div>
      <h3>Contact Us</h3>
      <p>Call us at 1-800-555-0187 or<br>fill out the online form</p>
    </div>
    <div class="how-step">
      <div class="how-icon" role="img" aria-label="Tow truck icon" style="background:linear-gradient(135deg,#e1251b,#1c3a6b);border-radius:50%;width:100px"></div>
      <div class="how-num">2</div>
      <h3>Schedule Pickup</h3>
      <p>We'll call you today to arrange a convenient<br>pickup time for your car donation.</p>
    </div>
    <div class="how-step">
      <div class="how-icon" role="img" aria-label="Tax receipt with ribbon icon" style="background:linear-gradient(135deg,#1c3a6b,#e1251b);border-radius:6px;width:90px"></div>
      <div class="how-num">3</div>
      <h3>Tax Deduction</h3>
      <p>You receive a tax receipt and<br>vacation voucher</p>
    </div>
  </div>
</section>

<section class="impact">
  <h2 class="section-title">Your Car Impacts Veterans' Lives</h2>
  <div class="impact-cards">
    <article class="impact-card">
      <div class="impact-photo" role="img" aria-label="Veterans standing with a flag" style="background:linear-gradient(135deg,#7b6a52,#b89c7a,#8a3a34)"></div>
      <h3>Help Us Reach Our Goal</h3>
      <p>Sed ut perspiciatis unde omnis iste natus error sit voluptatem accusantium doloremque laudant</p>
      <a href="#">Join Us</a>
    </article>
    <article class="impact-card">
      <div class="impact-photo" role="img" aria-label="Smiling young woman in a classroom" style="background:linear-gradient(135deg,#4a6e9a,#d8b48c,#e8dcc8)"></div>
      <h3>Vision</h3>
      <p>Sed ut perspiciatis unde omnis iste natus error sit voluptatem accusantium doloremque laudant</p>
      <a href="#">About Us</a>
    </article>
    <article class="impact-card">
      <div class="impact-photo" role="img" aria-label="Volunteers joining hands" style="background:linear-gradient(135deg,#6a3a2a,#c8927a,#f0e4da)"></div>
      <h3>On The Field</h3>
      <p>Sed ut perspiciatis unde omnis iste natus error sit voluptatem accusantium doloremque laudant</p>
      <a href="#">Volunteer</a>
    </article>
  </div>
</section>

<section class="why">
  <div class="why-photo" role="img" aria-label="Soldier embracing a family member in front of a flag"></div>
  <div class="why-copy">
    <h2>Why Donate Your Car To Us</h2>
    <ul class="why-list">
      <li><svg width="20" height="20" viewBox="0 0 20 20"><circle cx="10" cy="10" r="9" fill="#fff"/><path d="M6 10l3 3 5-6" stroke="#2a5a9c" stroke-width="2" fill="none"/></svg><span><b>IRS 501c(3) Approved</b> : Free 24/7 Pickup with No DMV Hassles.</span></li>
      <li><svg width="20" height="20" viewBox="0 0 20 20"><circle cx="10" cy="10" r="9" fill="#fff"/><path d="M6 10l3 3 5-6" stroke="#2a5a9c" stroke-width="2" fill="none"/></svg><span><b>Free Local Towing</b> : We will pick up your car donation, running or not, either at your business, at home or work.</span></li>
      <li><svg width="20" height="20" viewBox="0 0 20 20"><circle cx="10" cy="10" r="9" fill="#fff"/><path d="M6 10l3 3 5-6" stroke="#2a5a9c" stroke-width="2" fill="none"/></svg><span><b>Income Tax Deduction</b> : We insure you an IRS tax receipt and get you the highest tax write-off possible.</span></li>
      <li><svg width="20" height="20" viewBox="0 0 20 20"><circle cx="10" cy="10" r="9" fill="#fff"/><path d="M6 10l3 3 5-6" stroke="#2a5a9c" stroke-width="2" fill="none"/></svg><span><b>No Paperwork Hassles</b> : We handle everything: DMV and IRS paperwork.</span></li>
      <li><svg width="20" height="20" viewBox="0 0 20 20"><circle cx="10" cy="10" r="9" fill="#fff"/><path d="M6 10l3 3 5-6" stroke="#2a5a9c" stroke-width="2" fill="none"/></svg><span><b>Schedule a Free Pickup</b> : Complete the form and a representative will call you to arrange a convenient time to pick up your car.</span></li>
    </ul>
  </div>
</section>

<section class="faq">
  <h2 class="section-title">Frequently Asked Questions</h2>
  <div class="faq-list">
    <div class="faq-item is-open">
      <div class="faq-q">What types of vehicles can be donated?<svg width="14" height="9" viewBox="0 0 14 9"><path d="M1 8l6-6 6 6" stroke="#6b7280" stroke-width="2" fill="none"/></svg></div>
      <p>Nemo enim ipsam voluptatem quia voluptas sit aspernatur aut odit aut fugit, sed quia consequuntur magni dolores eos qui ratione voluptatem sequi nesciunt.</p>
    </div>
    <div class="faq-item">What paperwork do I need to donate my vehicle?<svg width="14" height="9" viewBox="0 0 14 9"><path d="M1 1l6 6 6-6" stroke="#6b7280" stroke-width="2" fill="none"/></svg></div>
    <div class="faq-item">Is my donated vehicle tax-deductible?<svg width="14" height="9" viewBox="0 0 14 9"><path d="M1 1l6 6 6-6" stroke="#6b7280" stroke-width="2" fill="none"/></svg></div>
    <div class="faq-item">What if the vehicle is not registered in my name?<svg width="14" height="9" viewBox="0 0 14 9"><path d="M1 1l6 6 6-6" stroke="#6b7280" stroke-width="2" fill="none"/></svg></div>
    <div class="faq-item">How much will I receive as a tax deduction for my vehicle?<svg width="14" height="9" viewBox="0 0 14 9"><path d="M1 1l6 6 6-6" stroke="#6b7280" stroke-width="2" fill="none"/></svg></div>
    <div class="faq-item">When will I receive my tax receipt?<svg width="14" height="9" viewBox="0 0 14 9"><path d="M1 1l6 6 6-6" stroke="#6b7280" stroke-width="2" fill="none"/></svg></div>
    <div class="faq-item">How do I schedule a pick up?<svg width="14" height="9" viewBox="0 0 14 9"><path d="M1 1l6 6 6-6" stroke="#6b7280" stroke-width="2" fill="none"/></svg></div>
  </div>
</section>

<footer class="site-footer">
  <div class="footer-brand">
    <a class="brand" href="#"><span class="brand-dot"></span><span class="brand-name">Wheels for Heroes</span></a>
    <p>Offers support and/or financial assistance to veterans and active military personnel and/or their family members who became newly blind and/or visually impaired from age-related macular degeneration, retinitis pigmentosa, glaucoma, keratoconus or diabetic retinopathy.</p>
  </div>
  <div class="footer-call">
    <small>Call Today To Donate</small>
    <strong>1-800-555-0187</strong>
    <span>Live Operators Available - 7 Days A Week</span>
    <div class="seals"><span class="seal square"></span><span class="seal"></span></div>
  </div>
  <div class="quick-links">
    <h4>Quick Links</h4>
    <ul><li>How To Donate</li><li>Why Donate</li><li>FAQ</li><li>About</li></ul>
  </div>
  <div class="footer-bar">
    <small>Copyright ©2020. Wheels for Heroes. All rights reserved.</small>
    <div class="social"><span></span><span></span><span></span><span></span></div>
  </div>
</footer>

</body>
</html>
```